Online Advice via Video Site requires Cutting Edge Homepage

We need a creative new and exciting webdesign for our tutoring via video-chat website.

We have prepared a "demo" homepage for you to see various promotional material that we think would be suitable for the homepage. http://www.quillmarsh.com/demo

The actual site is undergoing some final tinkering but can be accessed and used at http://www.quillmarsh.com

There is NO NEED to take any colours or design structure from this.

We expect the logo to be changed to match the new site. The new logo should match the site's function.

I have included some other projects that we like the look of:
http://www.vantoplex.com.au/design/143762
http://www.vantoplex.com.au/design/561630
http://www.vantoplex.com.au/design/247199
http://www.vantoplex.com.au/design/255195
http://www.birchlume.tv/

Target Market(s)

People that will work as tutors/advisers or be student/clients

Industry/Entity Type

Tutoring

Requirements
Must have
• The search is the main feature of the homepage

After the search the next goal of the page is to get people to sign up to the site

Login, (optional inclusion of the gablenet login - if you don't include it then you need only have a "login" button... no username or password input fields)

Footer
Nice to have
• The promotional material for the site, the colours on the Prezi file CAN BE changed to suit the new design you propose.

```html
<!DOCTYPE html>
<html lang="en">
<head>
<meta charset="utf-8">
<title>Quill Marsh – Homepage</title>
<link rel="stylesheet" href="https://fonts.googleapis.com/css2?family=Questrial&family=Open+Sans:wght@400&family=Arimo:wght@400;700&display=swap">
<style>
:root{
  --page:#f3f3f4;
  --ink:#222;
  --muted:#444;
  --blue:#1f5fae;
  --link-blue:#2d6bb8;
  --dark:#2f2f2f;
  --dark-2:#3b3b3b;
  --footer:#2a2a2a;
  --line:#d6d6d8;
  --panel:#ffffff;
  --soft:#e9e9eb;
  --sky:#5aa4e0;
}
*{box-sizing:border-box;margin:0;padding:0}
html,body{width:835px;height:1200px;overflow:hidden}
body{position:relative;background:linear-gradient(#fff 0,#f4f4f5 220px,#ececee 520px,#f4f4f5 1070px);font-family:"Arimo",Arial,sans-serif;color:var(--ink)}
.abs{position:absolute}
.brand{left:64px;top:30px;font-family:"Questrial",sans-serif;font-size:26px;color:#555;letter-spacing:-.5px}
.social-login{left:410px;top:34px;width:100px;height:40px;border:1px solid #cfcfd2;border-radius:3px;background:linear-gradient(#fff,#e8e8ea);display:flex;align-items:center;gap:8px;padding-left:8px;font-size:11px;color:var(--blue)}
.social-login .sq{width:22px;height:22px;background:var(--blue)}
.login-panel{left:522px;top:28px;width:301px;height:57px;background:var(--dark);border-radius:4px}
.field{position:absolute;top:12px;height:20px;background:#fff;border-radius:3px;font-size:9px;color:#aaa;padding:5px 10px}
.login-btn{position:absolute;left:228px;top:11px;width:63px;height:21px;border-radius:3px;background:linear-gradient(#555,#111);border:1px solid #777;color:#fff;font-size:12px;text-align:center;line-height:19px}
.login-panel .opt{position:absolute;top:39px;font-size:9px;color:#ddd}
.check{display:inline-block;width:8px;height:8px;background:#fff;margin-right:5px;vertical-align:-1px}
.main-nav{right:13px;top:106px;font-size:11.5px;color:#222;word-spacing:2px}
.main-nav .sep{margin:0 7px;color:#555}
.main-nav .current{color:var(--blue)}
.search-bar{left:13px;top:135px;width:811px;height:47px;background:linear-gradient(#444,var(--dark));border-radius:3px}
.search-label{position:absolute;left:165px;top:14px;color:#fff;font-size:15px}
.search-input{position:absolute;left:244px;top:10px;width:249px;height:22px;background:#f2f2f2;border-radius:3px;border:1px solid #999}
.search-btn{position:absolute;left:510px;top:10px;width:197px;height:23px;border:1px solid #888;border-radius:3px;background:linear-gradient(#555,#0d0d0d);color:#fff;font-size:12px;text-align:center;line-height:21px}
.drop-shadow{height:10px;border-radius:50%;background:radial-gradient(ellipse at center,rgba(0,0,0,.45),rgba(0,0,0,0) 70%)}
.hero{left:21px;top:212px;width:803px;height:289px;border:2px solid #d8d8da;border-radius:14px;background:linear-gradient(#fff 60%,#efeff1)}
.hero-person{left:95px;top:220px;width:141px;height:280px;background:linear-gradient(#4a4a4a,#2a2a2a);border-radius:60px 60px 0 0}
.hero-globe{left:282px;top:270px;width:228px;height:200px;border-radius:50%;background:radial-gradient(circle at 45% 45%,#d9eaf7,#eef5fb 60%,rgba(255,255,255,0) 72%)}
.hero-quote{left:270px;top:321px;width:500px;text-align:center;font-family:"Open Sans",sans-serif;font-size:20px;line-height:40px;color:#222}
.hero-quote .accent{color:var(--blue);font-size:23px}
.slide-arrow{top:357px}
.welcome{left:46px;top:531px;font-size:16px;color:#111}
.welcome span{color:var(--blue)}
.intro{left:50px;top:564px;width:470px;font-size:10px;line-height:15.5px;color:#555}
.points{left:73px;top:637px;list-style:none;font-size:11px;color:#222}
.points li{height:30px;position:relative;padding-left:20px}
.points li::before{content:"";position:absolute;left:1px;top:3px;width:6px;height:6px;background:var(--link-blue);transform:rotate(45deg)}
.rule{left:90px;top:771px;width:430px;height:3px;background:radial-gradient(ellipse at center,#c6c6c8,rgba(0,0,0,0) 70%)}
.card{background:var(--panel);border:1px solid var(--line);border-radius:3px;box-shadow:0 1px 2px rgba(0,0,0,.08)}
.advisors{left:590px;top:531px;width:225px;height:250px}
.advisor-icon{position:absolute;left:24px;top:4px;width:30px;height:32px;background:linear-gradient(#555,#222);border-radius:12px 12px 3px 3px}
.card-title{position:absolute;font-size:15px;color:var(--blue)}
.adv-list{position:absolute;left:16px;top:47px;list-style:none;font-size:10px;color:#222}
.adv-list li{height:20px;position:relative;padding-left:10px}
.adv-list li.sub{margin-left:26px}
.adv-list li.gap{margin-top:10px}
.adv-list li::before{content:"›";position:absolute;left:0;top:-3px;font-size:13px;font-weight:700}
.features{left:27px;top:806px;width:796px;height:248px}
.tab-bar{position:absolute;left:9px;top:10px;width:565px;height:30px;border:1px solid #cdcdcf;border-radius:3px;background:linear-gradient(#fff,#e4e4e6);font-size:11px;color:#222}
.tab-bar span{position:absolute;top:8px}
.tab-bar .active{color:var(--blue)}
.feature-list{position:absolute;left:45px;top:50px;list-style:none;font-size:10px;color:#222}
.feature-list li{height:20px}
.topics-bar{position:absolute;left:9px;top:144px;width:565px;height:31px;border:1px solid #cdcdcf;border-radius:3px;background:linear-gradient(#fff,#e4e4e6);font-size:11px;color:var(--blue);padding:9px 18px}
.topic{position:absolute;font-size:10px;color:#222}
.testimonials{left:610px;top:818px;width:202px;height:222px;background:linear-gradient(#fff,#f0f0f2);border:1px solid #cfcfd1;border-radius:8px;box-shadow:0 2px 3px rgba(0,0,0,.2)}
.note-icon{position:absolute;left:9px;top:7px;width:27px;height:30px;background:#e6e6e8;border:1px solid #bbb}
.avatar{position:absolute;left:6px;width:42px;height:40px;background:#d4d4d6;border-radius:20px 20px 2px 2px}
.quote{position:absolute;left:52px;width:140px;font-size:10px;line-height:14px;color:#333}
.quote .who{display:block;margin-top:2px;padding-left:2px;color:#555}
.more{position:absolute;left:158px;top:198px;font-size:10px;color:var(--blue)}
.site-footer{left:0;top:1076px;width:835px;height:124px;background:var(--footer)}
.connect{position:absolute;left:48px;top:32px;font-size:11px;color:var(--sky)}
.social{position:absolute;left:48px;top:66px;display:flex;gap:4px}
.social span{width:22px;height:22px;border-radius:3px;background:#5d5d60}
.foot-nav{position:absolute;right:27px;top:35px;font-size:9px;color:#ddd}
.copy{position:absolute;right:23px;top:70px;font-size:9px;color:#ddd}
</style>
</head>
<body>

<div class="abs brand">Quill Marsh</div>

<div class="abs social-login"><span class="sq"></span>gablenet LOGIN</div>

<div class="abs login-panel">
  <div class="field" style="left:9px;width:96px">User Name</div>
  <div class="field" style="left:118px;width:97px">Password</div>
  <div class="login-btn">Login</div>
  <div class="opt" style="left:15px"><span class="check"></span>Remember Me</div>
  <div class="opt" style="left:129px">Forgot it?</div>
</div>

<nav class="abs main-nav">
  <span class="current">Home</span><span class="sep">|</span>Student<span class="sep">|</span>Advisors<span class="sep">|</span>Topics<span class="sep">|</span>Blog<span class="sep">|</span>FAQs<span class="sep">|</span>Sitemap<span class="sep">|</span>About us<span class="sep">|</span>Our Technology<span class="sep">|</span>Contact
</nav>

<div class="abs search-bar">
  <div class="search-label">SEARCH</div>
  <div class="search-input">
    <svg width="22" height="18" style="position:absolute;left:4px;top:2px"><circle cx="8" cy="8" r="5" fill="none" stroke="#888" stroke-width="1.6"/><line x1="12" y1="12" x2="17" y2="16" stroke="#888" stroke-width="2"/></svg>
  </div>
  <div class="search-btn">SEARCH TOPICS &amp; ADVISORS</div>
</div>
<div class="abs drop-shadow" style="left:60px;top:182px;width:730px"></div>

<section class="abs hero"></section>
<div class="abs hero-globe" role="img" aria-label="Illustration of a pale blue globe with an e-learning arrow"></div>
<div class="abs hero-person" role="img" aria-label="Photo of a smiling businesswoman in a dark suit with arms crossed"></div>
<div class="abs hero-quote">"Imagine if, whenever you had a problem you could<br>instantly access the world's experts to solve it.<br><span class="accent">Now you can!</span>"</div>
<svg class="abs slide-arrow" style="left:26px" width="24" height="24"><circle cx="12" cy="12" r="11" fill="#9a9a9c"/><circle cx="12" cy="12" r="8" fill="#d4d4d6"/><path d="M15 12H8M11 8l-4 4 4 4" stroke="#555" stroke-width="2" fill="none"/></svg>
<svg class="abs slide-arrow" style="left:795px" width="24" height="24"><circle cx="12" cy="12" r="11" fill="#9a9a9c"/><circle cx="12" cy="12" r="8" fill="#d4d4d6"/><path d="M8 12h7M12 8l4 4-4 4" stroke="#555" stroke-width="2" fill="none"/></svg>
<div class="abs drop-shadow" style="left:260px;top:502px;width:400px"></div>

<h1 class="abs welcome" style="font-weight:400">WELCOME TO&nbsp; QUILL <span>MARSH</span></h1>
<p class="abs intro">Lorem Ipsum is simply dummy text of the printing and typesetting industry. Lorem Ipsum has been the industry's standard dummy text ever since the 1500s, when an unknown printer took a galley of type and scrambled it to make a type specimen book.</p>
<ul class="abs points">
  <li>QuillMarsh is the place for e-learning, mentoring &amp; professional advice</li>
  <li>It instantly connects people with knowledge and those who need it</li>
  <li>Connects people for ongoing advice or on off answers</li>
  <li>Ask questions and/or work exactly when it suits you</li>
</ul>
<div class="abs rule"></div>

<aside class="abs card advisors">
  <div class="advisor-icon" role="img" aria-label="Small icon of an advisor in a suit"></div>
  <div class="card-title" style="left:64px;top:13px">ADVISORS</div>
  <ul class="adv-list">
    <li>Teach the topics you know well</li>
    <li>Educate people in your spare time</li>
    <li class="sub">Answer single questions</li>
    <li class="sub">Provide ongoing tutoring</li>
    <li class="gap">Work when it suits you</li>
    <li class="sub">Pre-book appointments</li>
    <li class="sub">Answer questions only when you can</li>
    <li class="gap">Earn money for your time</li>
    <li>Set your own fee rate</li>
  </ul>
</aside>

<section class="abs card features">
  <div class="tab-bar">
    <span class="active" style="left:11px">Instant Personal Advice</span>
    <span style="left:155px">Direct Video Conference</span>
    <span style="left:300px">Advisors and/or Clients</span>
    <span style="left:439px">Paywren Or Credit Card</span>
  </div>
  <ul class="feature-list">
    <li>Find advisors</li>
    <li>Waiting online</li>
    <li>OR</li>
    <li>Book appointment when it suits</li>
  </ul>
  <div class="topics-bar">ADVISORS BY TOPICS</div>
  <span class="topic" style="left:30px;top:190px">English</span>
  <span class="topic" style="left:131px;top:190px">Building</span>
  <span class="topic" style="left:274px;top:190px">Cultural Studies</span>
  <span class="topic" style="left:425px;top:190px">Criminology</span>
  <span class="topic" style="left:30px;top:210px">Agriculture</span>
  <span class="topic" style="left:131px;top:210px">Veterinary Science</span>
</section>

<aside class="abs testimonials">
  <div class="note-icon" role="img" aria-label="Small notepad and pencil icon"></div>
  <div class="card-title" style="left:43px;top:14px">Testimonials</div>
  <div class="avatar" style="top:50px" role="img" aria-label="Placeholder avatar silhouette"></div>
  <p class="quote" style="top:56px">Nunc varius facilisis eros. Sed rat. In in velit quis arcu ornare laoreet. luctus massa.<span class="who">John</span></p>
  <div class="avatar" style="top:135px" role="img" aria-label="Placeholder avatar silhouette"></div>
  <p class="quote" style="top:132px">Nunc varius facilisis eros. Sed rat. In in velit quis arcu ornare laoreet. luctus massa.<span class="who">John</span></p>
  <span class="more">More</span>
</aside>

<footer class="abs site-footer">
  <div class="connect">CONNECT WITH US</div>
  <div class="social"><span></span><span></span><span></span><span></span></div>
  <div class="foot-nav">Home | Student | Advisors | Topics | Blog | FAQs | Sitemap | About us | Our Technology | Contact</div>
  <div class="copy">© 2012 quillmarsh. All rights reserved.</div>
</footer>

</body>
</html>
```